Business card for medical clinic

I need an upmarket, modern medical/health business card for my clinic

Contact Information for Business Card

name, address, email, qr code

```html
<!DOCTYPE html>
<html lang="en">
<head>
<meta charset="utf-8">
<title>Meridale Care Partners – Business Card</title>
<link rel="stylesheet" href="https://fonts.googleapis.com/css2?family=Poppins:wght@300;400;500;700&display=swap">
<style>
  :root {
    --backdrop: #212121;
    --card: #1d1e22;
    --card-deep: #17181b;
    --band-shadow: rgba(0, 0, 0, 0.55);
    --brand-blue: #2a9fd9;
    --brand-blue-soft: #3aaee6;
    --ink-light: #f2f4f6;
    --pattern-a: #2a2b30;
    --pattern-b: #1a1b1f;
  }
  * { box-sizing: border-box; margin: 0; padding: 0; }
  html, body { width: 1200px; height: 780px; overflow: hidden; }
  body {
    background: var(--backdrop);
    font-family: "Poppins", sans-serif;
    display: flex;
    align-items: center;
    justify-content: center;
    gap: 48px;
  }
  .card {
    position: relative;
    width: 540px;
    height: 309px;
    background: var(--card);
    border-radius: 3px;
    overflow: hidden;
    box-shadow: 0 18px 40px rgba(0, 0, 0, 0.5);
  }

  /* Front: contact side */
  .card-front .shadow-band {
    position: absolute;
    left: -40px;
    right: -40px;
    top: 92px;
    height: 110px;
    background: linear-gradient(180deg, rgba(0,0,0,0) 0%, var(--band-shadow) 50%, rgba(0,0,0,0) 100%);
    transform: rotate(-4deg);
    opacity: 0.7;
  }
  .brand-mini {
    position: absolute;
    left: 150px;
    top: 32px;
    display: flex;
    align-items: center;
    gap: 10px;
  }
  .brand-mini .brand-dot {
    width: 38px; height: 38px;
    border: 2px solid var(--brand-blue);
    border-radius: 50%;
  }
  .brand-name {
    font-weight: 500;
    color: var(--brand-blue);
    letter-spacing: 0.06em;
    text-transform: uppercase;
  }
  .brand-mini .brand-name { font-size: 14px; }

  .person {
    position: absolute;
    left: 150px;
    top: 100px;
  }
  .person-name {
    font-size: 30px;
    line-height: 1.1;
    color: var(--brand-blue);
    font-weight: 300;
  }
  .person-name .first { font-weight: 700; }
  .person-title {
    font-size: 12px;
    font-weight: 500;
    color: var(--ink-light);
    margin-top: 2px;
  }

  .contact-list {
    position: absolute;
    left: 150px;
    top: 178px;
    list-style: none;
    display: flex;
    flex-direction: column;
    gap: 6px;
  }
  .contact-item {
    display: flex;
    align-items: center;
    gap: 10px;
    font-size: 11.5px;
    color: var(--ink-light);
    font-weight: 400;
  }
  .contact-icon {
    width: 18px; height: 18px;
    border-radius: 50%;
    background: var(--brand-blue-soft);
    display: flex; align-items: center; justify-content: center;
    flex-shrink: 0;
  }
  .contact-icon svg { width: 10px; height: 10px; }

  .address {
    position: absolute;
    left: 0; right: 0;
    bottom: 22px;
    text-align: center;
    font-size: 12px;
    color: var(--brand-blue);
    display: flex; align-items: center; justify-content: center; gap: 8px;
  }

  /* Back: brand side */
  .card-back .pattern-field {
    position: absolute;
    inset: 0;
    background: radial-gradient(circle at 70% 30%, var(--pattern-a) 0%, var(--pattern-b) 75%);
  }
  .brand-main {
    position: absolute;
    inset: 0;
    display: flex;
    align-items: center;
    justify-content: center;
    gap: 16px;
  }
  .brand-main .brand-dot {
    width: 70px; height: 70px;
    border: 3px solid var(--brand-blue);
    border-radius: 50%;
  }
  .brand-main .brand-name { font-size: 26px; }
</style>
</head>
<body>

  <section class="card card-front" aria-label="Business card, contact side">
    <div class="shadow-band"></div>

    <div class="brand-mini">
      <span class="brand-dot"></span>
      <span class="brand-name">Meridale Care Partners</span>
    </div>

    <div class="person">
      <h1 class="person-name"><span class="first">Lena</span> Marovic</h1>
      <p class="person-title">Founder &amp; CEO</p>
    </div>

    <ul class="contact-list">
      <li class="contact-item">
        <span class="contact-icon">
          <svg viewBox="0 0 24 24"><path fill="#fff" d="M6.6 10.8a15 15 0 0 0 6.6 6.6l2.2-2.2c.3-.3.7-.4 1-.2 1.1.4 2.3.6 3.6.6.6 0 1 .4 1 1V20c0 .6-.4 1-1 1A17 17 0 0 1 3 4c0-.6.4-1 1-1h3.5c.6 0 1 .4 1 1 0 1.3.2 2.5.6 3.6.1.3 0 .7-.2 1z"/></svg>
        </span>
        (555) 014-2290
      </li>
      <li class="contact-item">
        <span class="contact-icon">
          <svg viewBox="0 0 24 24"><path fill="#fff" d="M3 5h18v14H3z M4 6l8 6 8-6" stroke="#3aaee6" stroke-width="2"/></svg>
        </span>
        hello@meridalecare.com
      </li>
      <li class="contact-item">
        <span class="contact-icon">
          <svg viewBox="0 0 24 24"><circle cx="12" cy="12" r="9" fill="none" stroke="#fff" stroke-width="2"/><path d="M3 12h18M12 3c3 3 3 15 0 18M12 3c-3 3-3 15 0 18" fill="none" stroke="#fff" stroke-width="1.6"/></svg>
        </span>
        www.meridalecare.com
      </li>
    </ul>

    <p class="address">
      <span class="contact-icon">
        <svg viewBox="0 0 24 24"><path fill="#fff" d="M12 2a7 7 0 0 0-7 7c0 5 7 13 7 13s7-8 7-13a7 7 0 0 0-7-7zm0 9.5A2.5 2.5 0 1 1 12 6.5a2.5 2.5 0 0 1 0 5z"/></svg>
      </span>
      480 Willowbend Ave. Suite 120 Northfield, TX 75001
    </p>
  </section>

  <section class="card card-back" aria-label="Business card, brand side">
    <div class="pattern-field" role="img" aria-label="Embossed repeating brand-mark pattern across the card"></div>
    <div class="brand-main">
      <span class="brand-dot"></span>
      <span class="brand-name">Meridale Care Partners</span>
    </div>
  </section>

</body>
</html>
```